Varnik Holdings — Business Card Design Brief
Overview
Design a double-sided business card for Varnik Holdings that highlights our two service arms: Varnik Communications (telecommunications) and Varnik Energy (business energy solutions). The card should feel smart and stand out when handed to clients.

Objectives
Showcase our areas of specialty clearly.
Reflect the overall Varnik / Varnik Holdings brand while acknowledging both arms.
Explore using both logos (Communications + Energy) or one unified logo, depending on the design.

Deliverables
One double-sided business card design (front + back).

Content & Copy
Front (preferred): Logo: Varnik / Varnik Holdings
Descriptor: Business Communications | Business Energy
Back:My contact details and company details
Core products: Business Mobile • Telephony • Internet • Business Energy Solutions

Brand & Visual Direction
We have a group logo currently tailored more toward telecoms, plus a separate Varnik Energy logo.
Please explore layouts that use both logos or just one, whichever works best.
Color: I wouldn't mind seeing an option using our the Blue/Purple gradient from our website (varnik-example.co.uk), but also open to non-gradient approaches and other colours..

Overall look: Smart, modern, and distinctive.
Format & Print Specs
Double-sided business card format. (Use a standard size

Must-Haves
Front: Varnik wording or Varnik Holdings wording with atleast 1 logo also on front “Business Communications | Business Energy.”

Back: Contact + company details and core products.
A design that stands out while remaining professional.

Nice-to-Have Options
A gradient version using our site’s Blue/Purple gradient.
A non-gradient version.
A dual-logo treatment versus a single-logo treatment.

Thanks
Owen

```html
<!DOCTYPE html>
<html lang="en">
<head>
<meta charset="utf-8">
<title>Varnik Holdings — Business Card</title>
<link href="https://fonts.googleapis.com/css2?family=Roboto:wght@400;500;700&display=swap" rel="stylesheet">
<style>
  :root{
    --page:#e6e6e6;
    --white:#ffffff;
    --navy:#1c1464;
    --navy-ink:#1f1566;
    --stripe:#1a6fe0;
    --green:#8dc21f;
    --sky:#0bb5e0;
    --royal:#0a58d2;
  }
  *{margin:0;padding:0;box-sizing:border-box}
  html,body{width:1200px;height:1200px;overflow:hidden;background:var(--page);font-family:"Roboto",Arial,sans-serif}
  .card{position:absolute;left:256px;width:688px;height:393px;overflow:hidden}
  .card-front{top:158px;display:flex;background:var(--white)}
  .brand-panel{width:372px;height:100%;display:flex;align-items:center;justify-content:center;gap:16px}
  .brand-dot{width:46px;height:46px;border-radius:50%;background:var(--green)}
  .brand-name{font-size:58px;font-weight:700;color:var(--navy-ink);letter-spacing:1px}
  .brand-stripe{width:8px;height:100%;background:var(--stripe)}
  .details-panel{flex:1;background:var(--navy);color:var(--white);padding:50px 0 0 46px}
  .person-name{font-size:27px;font-weight:700;color:var(--green);letter-spacing:.5px;line-height:1}
  .person-role{font-size:16px;margin-top:6px}
  .address{font-size:16.5px;line-height:21px;margin-top:18px}
  .contact-list{list-style:none;margin-top:12px}
  .contact-list li{display:flex;align-items:center;gap:12px;font-size:16.5px;line-height:20.5px}
  .contact-list svg{width:13px;height:13px;flex:none}
  .product-list{list-style:none;margin-top:10px}
  .product-list li{font-size:17px;line-height:21.5px}
  .product-list li::before{content:"•";margin-right:7px}
  .card-back{top:652px;background:linear-gradient(180deg,var(--sky) 0%,var(--royal) 100%);color:var(--white)}
  .arm{position:absolute;top:126px;width:344px;display:flex;flex-direction:column;align-items:center}
  .arm-comms{left:0}
  .arm-energy{right:0}
  .arm-mark{display:flex;align-items:center;gap:12px;height:118px}
  .arm-dot{width:40px;height:40px;border-radius:50%;background:var(--white)}
  .arm-name{font-size:38px;font-weight:700}
  .arm-label{font-size:17px;letter-spacing:.2px;margin-top:10px}
  .arm-divider{position:absolute;left:343px;top:113px;width:2px;height:168px;background:rgba(255,255,255,.85)}
</style>
</head>
<body>
  <section class="card card-front">
    <div class="brand-panel">
      <span class="brand-dot"></span>
      <span class="brand-name">VARNIK</span>
    </div>
    <div class="brand-stripe"></div>
    <div class="details-panel">
      <p class="person-name">DANIEL REEVE</p>
      <p class="person-role">President</p>
      <p class="address">4120 Alder Court<br>Halton, Canada 58210</p>
      <ul class="contact-list">
        <li><svg viewBox="0 0 16 16"><path fill="#8dc21f" d="M3 1l3 3-2 2c1 2 3 4 5 5l2-2 3 3-2 3C6 15 1 10 0 4z"/></svg>555-201-4736</li>
        <li><svg viewBox="0 0 16 16"><rect x="4" y="1" width="8" height="14" rx="1.5" fill="none" stroke="#8dc21f" stroke-width="2"/></svg>555-318-9024</li>
        <li><svg viewBox="0 0 16 16"><rect x="1" y="4" width="14" height="9" fill="#8dc21f"/><path d="M1 4l7 5 7-5" fill="none" stroke="#1c1464" stroke-width="1.3"/></svg>info@varnik-example.co.uk</li>
        <li><svg viewBox="0 0 16 16"><circle cx="8" cy="8" r="7" fill="#8dc21f"/><path d="M4 5c2 0 3 1 3 3s-2 2-2 4M10 3c0 2 2 2 3 3" fill="none" stroke="#1c1464" stroke-width="1.3"/></svg>www.varnik-example.co.uk</li>
      </ul>
      <ul class="product-list">
        <li>Business Mobile</li>
        <li>Telephony</li>
        <li>Internet</li>
        <li>Business Energy Solutions</li>
      </ul>
    </div>
  </section>

  <section class="card card-back">
    <div class="arm arm-comms">
      <div class="arm-mark"><span class="arm-dot"></span><span class="arm-name">Varnik</span></div>
      <p class="arm-label">BUSINESS COMMUNICATIONS</p>
    </div>
    <div class="arm-divider"></div>
    <div class="arm arm-energy">
      <div class="arm-mark"><span class="arm-dot"></span><span class="arm-name">Varnik</span></div>
      <p class="arm-label">BUSINESS ENERGY</p>
    </div>
  </section>
</body>
</html>
```